The K7 Momentum Collective Website

We have a pitch deck and messaging drafted. Target audience is academic institutions and VC investors that have seed money in start ups.

Need a basic website

Industry/Entity Type

LIfe Science, Diagnostic, medical device.

Coding

Coded - Design and coding required

Number of Pages Required

5+ page

```html
<!DOCTYPE html>
<html lang="en">
<head>
<meta charset="utf-8">
<title>The K7 Momentum Collective</title>
<link href="https://fonts.googleapis.com/css2?family=Kanit:wght@500;600&family=Roboto:wght@400;500;700&display=swap" rel="stylesheet">
<style>
:root{
  --blue:#0a63b8;
  --blue-dark:#08539c;
  --sky:#eef6fc;
  --ink:#1d1d1f;
  --muted:#6b6b6b;
  --white:#ffffff;
  --footer:#2c2c2c;
  --footer-line:#4a4a4a;
}
*{box-sizing:border-box;margin:0;padding:0}
html,body{width:1200px;height:4033px;overflow:hidden}
body{position:relative;font-family:'Roboto',Arial,sans-serif;color:var(--ink);background:var(--white)}
section,header,footer{position:absolute;left:0;width:1200px}
.heading{font-family:'Kanit',Arial,sans-serif;font-weight:500;color:var(--ink)}
.btn{position:absolute;display:flex;align-items:center;justify-content:center;gap:8px;font-weight:700;font-size:15px;text-transform:uppercase;border-radius:3px}
.btn-blue{background:var(--blue);color:var(--white)}
.btn-white{background:var(--white);color:var(--blue)}
.btn svg{width:15px;height:15px}

/* header */
.site-header{top:0;height:85px;background:var(--white);z-index:3;box-shadow:0 1px 0 #e5e5e5}
.brand{position:absolute;left:108px;top:30px;display:flex;align-items:center;gap:8px;font-family:'Kanit',Arial,sans-serif;font-weight:600;font-size:17px;color:var(--blue);text-transform:uppercase;letter-spacing:.2px}
.brand-dot{width:14px;height:14px;border-radius:50%;background:var(--blue)}
.nav{position:absolute;top:33px;left:0;font-size:15px;text-transform:uppercase;color:#3a3a3a}
.nav span{position:absolute;white-space:nowrap}
.nav .active{color:var(--blue);font-weight:500;border-bottom:1px solid var(--blue)}
.login{left:956px;top:20px;width:131px;height:43px}

/* hero */
.hero{top:85px;height:693px}
.hero-photo{position:absolute;inset:0;background:linear-gradient(100deg,#1d3550 0%,#2f4f6e 35%,#5b7590 60%,#8a9fb3 100%)}
.hero-title{position:absolute;left:106px;top:180px;font-family:'Kanit',Arial,sans-serif;font-weight:600;font-size:64px;line-height:75px;color:var(--white)}
.get-started{left:106px;top:448px;width:171px;height:51px}

/* about */
.about{top:778px;height:586px}
.about-frame{position:absolute;left:111px;top:104px;width:459px;height:382px;border:2px solid var(--blue);padding:13px 11px}
.about-photo{width:100%;height:100%;background:linear-gradient(120deg,#c9b8a6,#e8e4df 50%,#b9c6d2)}
.about-title{position:absolute;left:645px;top:102px;width:440px;font-size:32px;line-height:34px}
.about-text{position:absolute;left:645px;top:180px;width:444px;font-size:14.5px;line-height:25.6px;color:var(--muted);text-align:justify}
.learn-about{left:645px;top:434px;width:156px;height:46px}

/* partners */
.partners{top:1364px;height:586px;background:var(--sky)}
.section-title{position:absolute;left:0;width:1200px;text-align:center;font-size:33px}
.partner{position:absolute;top:157px;width:275px;height:350px;background:var(--white);border:1px solid #dfe6ec}
.partner-photo{width:100%;height:289px}
.partner-name{height:60px;display:flex;align-items:center;justify-content:center;font-size:18.5px;font-weight:500}
.partner-bio{width:100%;height:289px;background:var(--blue);color:var(--white);font-size:14.5px;line-height:29px;text-align:center;padding:70px 28px 0}

/* problem */
.problem{top:1950px;height:513px}
.problem-panel{position:absolute;left:0;top:0;width:598px;height:513px;background:var(--blue)}
.problem-photo{position:absolute;left:598px;top:0;width:602px;height:513px;background:linear-gradient(135deg,#6c7a89,#b7b3ad 50%,#d9d2c6)}
.problem-title{position:absolute;left:106px;top:68px;font-size:32px;color:var(--white)}
.problem-lead{position:absolute;left:106px;top:128px;width:440px;font-size:15.5px;line-height:26px;color:var(--white)}
.problem-list{position:absolute;left:106px;top:191px;width:400px;list-style:none;color:var(--white);font-size:15.5px;line-height:24px}
.problem-list li{position:relative;padding-left:29px;margin-bottom:14px;display:flex;align-items:center}
.problem-list svg{position:absolute;left:0;top:50%;margin-top:-8px;width:16px;height:16px}
.learn-problem{left:106px;top:391px;width:157px;height:46px}

/* discovery */
.discovery{top:2463px;height:571px}
.disc-card{position:absolute;top:226px;width:311px;height:232px;background:var(--white);border:1px solid #dcdcdc;box-shadow:0 4px 10px rgba(0,0,0,.05);text-align:center}
.disc-icon{position:absolute;top:169px;width:118px;height:118px;border:2px dashed var(--blue);padding:7px;background:var(--white)}
.disc-icon div{width:100%;height:100%;background:var(--blue);display:flex;align-items:center;justify-content:center}
.disc-card h3{margin-top:86px;font-size:18.5px;font-weight:500}
.disc-card p{margin:14px auto 0;width:270px;font-size:14px;line-height:24px;color:var(--muted)}
.disc-go{position:absolute;top:439px;width:40px;height:40px;border-radius:50%;background:var(--blue);border:4px solid var(--white);box-shadow:0 2px 6px rgba(0,0,0,.2);display:flex;align-items:center;justify-content:center}
.arrow{position:absolute;top:310px;width:24px;height:30px}

/* plan */
.plan{top:3034px;height:624px;background:var(--blue)}
.plan .section-title{color:var(--white);top:60px}
.pill{position:absolute;width:452px;height:148px;background:var(--white);border-radius:74px;box-shadow:0 6px 14px rgba(0,0,0,.18);overflow:hidden}
.pill-photo{position:absolute;left:6px;top:5px;width:138px;height:138px;border-radius:50%;border:4px solid var(--white);box-shadow:0 2px 8px rgba(0,0,0,.25)}
.pill h4{position:absolute;left:170px;top:22px;font-size:15px;font-weight:700}
.pill p{position:absolute;left:170px;top:46px;width:266px;font-size:13px;line-height:21px;color:var(--muted)}
.view-more{left:523px;top:510px;width:154px;height:47px}

/* footer */
.site-footer{top:3658px;height:375px;background:var(--footer);color:var(--white)}
.footer-brand{position:absolute;left:114px;top:116px;display:flex;align-items:center;gap:8px;font-family:'Kanit',Arial,sans-serif;font-weight:600;font-size:17px;color:#3d8be0;text-transform:uppercase}
.socials{position:absolute;left:163px;top:209px;display:flex;gap:6px}
.socials span{width:22px;height:22px;border-radius:50%;border:1.5px solid var(--white)}
.f-col{position:absolute;top:62px}
.f-col h5{font-size:17px;font-weight:700;margin-bottom:22px}
.f-col li{list-style:none;font-size:14px;line-height:26px;color:#e5e5e5}
.contact-item{position:relative;padding-left:28px;margin-bottom:18px}
.contact-item svg{position:absolute;left:0;top:1px;width:16px;height:16px}
.contact-item b{display:block;font-size:12.5px;font-weight:700}
.contact-item span{display:block;font-size:14px;line-height:19px;color:#e5e5e5}
.f-rule{position:absolute;left:110px;top:303px;width:980px;height:1px;background:var(--footer-line)}
.copyright{position:absolute;left:0;top:324px;width:1200px;text-align:center;font-size:13.5px;color:#e5e5e5}
.to-top{position:absolute;left:1124px;top:282px;width:36px;height:36px;border-radius:50%;background:var(--blue);display:flex;align-items:center;justify-content:center}
</style>
</head>
<body>

<header class="site-header">
  <div class="brand"><span class="brand-dot"></span>The K7 Momentum Collective</div>
  <nav class="nav">
    <span class="active" style="left:479px">Home</span>
    <span style="left:554px">About Us</span>
    <span style="left:657px">Services</span>
    <span style="left:756px">Team</span>
    <span style="left:850px">Contact Us</span>
  </nav>
  <a class="btn btn-blue login">Login
    <svg viewBox="0 0 16 16"><rect x="3" y="7" width="10" height="8" rx="1" fill="#fff"/><path d="M5 7V5a3 3 0 0 1 6 0v2" stroke="#fff" stroke-width="2" fill="none"/></svg>
  </a>
</header>

<section class="hero">
  <div class="hero-photo" role="img" aria-label="Executive reviewing documents at a desk with a laptop in a bright office"></div>
  <h1 class="hero-title">THe K7<br>Momentum<br>Collective</h1>
  <a class="btn btn-blue get-started">Get Started
    <svg viewBox="0 0 16 16"><circle cx="8" cy="8" r="8" fill="#fff"/><path d="M6.5 4.5 10 8l-3.5 3.5" stroke="#0a63b8" stroke-width="2" fill="none"/></svg>
  </a>
</section>

<section class="about">
  <div class="about-frame"><div class="about-photo" role="img" aria-label="Colleagues shaking hands across a meeting table"></div></div>
  <h2 class="heading about-title">About The K7 Momentum Collective</h2>
  <p class="about-text">The K7 Momentum Collective (K7) is a group of experienced executives whose careers have been focused on taking innovative ideas to market by strategically navigating the buildout of best-in-class life science and diagnostic organizations. This experience makes us uniquely equipped to be involved in all aspects of your due diligence on new or existing investments (business analysis, industry thesis, competitive landscape, business/pricing model, and financial modeling as it relates to validation of the assumptions in the model to determine the return expectations).</p>
  <a class="btn btn-blue learn-about">Learn More
    <svg viewBox="0 0 16 16"><circle cx="8" cy="8" r="8" fill="#fff"/><path d="M6.5 4.5 10 8l-3.5 3.5" stroke="#0a63b8" stroke-width="2" fill="none"/></svg>
  </a>
</section>

<section class="partners">
  <h2 class="heading section-title" style="top:70px">Meet The Partners</h2>
  <div class="partner" style="left:169px">
    <div class="partner-photo" role="img" aria-label="Portrait of partner Dana Whitfield" style="background:linear-gradient(160deg,#c8b48e,#8a8a5a 55%,#2f5a4a)"></div>
    <div class="partner-name">Dana Whitfield</div>
  </div>
  <div class="partner" style="left:466px">
    <div class="partner-bio">RJ is an accomplished CEO and well-rounded executive with more than 25 years of experience in medicaldevices, research tools and diagnostics.</div>
    <div class="partner-name">RJ Morrow</div>
  </div>
  <div class="partner" style="left:763px">
    <div class="partner-photo" role="img" aria-label="Portrait of partner LC Haines" style="background:linear-gradient(160deg,#d6dde3,#a9b4bd 50%,#3b3f46)"></div>
    <div class="partner-name">LC Haines</div>
  </div>
</section>

<section class="problem">
  <div class="problem-panel"></div>
  <div class="problem-photo" role="img" aria-label="Mentor guiding a team working at computers in an office"></div>
  <h2 class="heading problem-title" style="color:#fff">The Problem &gt; The Solution</h2>
  <p class="problem-lead">K7 was started to solve significant problems associated with rapidly bringing innovative and transformational IP to market.</p>
  <ul class="problem-list">
    <li><svg viewBox="0 0 16 16"><circle cx="8" cy="8" r="8" fill="#fff"/><path d="M4.5 8.2 7 10.5l4.5-5" stroke="#0a63b8" stroke-width="2" fill="none"/></svg>Incomplete strategic planning,</li>
    <li><svg viewBox="0 0 16 16"><circle cx="8" cy="8" r="8" fill="#fff"/><path d="M4.5 8.2 7 10.5l4.5-5" stroke="#0a63b8" stroke-width="2" fill="none"/></svg>Difficulty finding leadership,</li>
    <li><svg viewBox="0 0 16 16"><circle cx="8" cy="8" r="8" fill="#fff"/><path d="M4.5 8.2 7 10.5l4.5-5" stroke="#0a63b8" stroke-width="2" fill="none"/></svg>Not able to differentiate a product or service from others that are already available, and</li>
    <li><svg viewBox="0 0 16 16"><circle cx="8" cy="8" r="8" fill="#fff"/><path d="M4.5 8.2 7 10.5l4.5-5" stroke="#0a63b8" stroke-width="2" fill="none"/></svg>Ignoring the needs of customer.</li>
  </ul>
  <a class="btn btn-white learn-problem">Learn More
    <svg viewBox="0 0 16 16"><circle cx="8" cy="8" r="8" fill="#0a63b8"/><path d="M6.5 4.5 10 8l-3.5 3.5" stroke="#fff" stroke-width="2" fill="none"/></svg>
  </a>
</section>

<section class="discovery">
  <h2 class="heading section-title" style="top:80px">Discovery to Market</h2>
  <svg class="arrow" style="left:44px" viewBox="0 0 24 30"><path d="M16 4 6 15l10 11" stroke="#555" stroke-width="2.5" fill="none"/></svg>
  <svg class="arrow" style="left:1132px" viewBox="0 0 24 30"><path d="M8 4l10 11L8 26" stroke="#555" stroke-width="2.5" fill="none"/></svg>

  <div class="disc-card" style="left:108px"><h3>Innovative IP</h3><p>Inventor DisclosureProvisional Patent Licensing agreement</p></div>
  <div class="disc-card" style="left:443px"><h3>Strategic Business Plan</h3><p>Invention AssessmentVoice of Customer Product DefinitionBusiness Model/Plan Pitch Deck</p></div>
  <div class="disc-card" style="left:776px"><h3>Company Formation</h3><p>Experienced management How to build out the initial team Product definition Business model Org structure</p></div>

  <div class="disc-icon" style="left:205px"><div>
    <svg width="60" height="60" viewBox="0 0 60 60" fill="none" stroke="#fff" stroke-width="2.5"><circle cx="30" cy="26" r="14"/><circle cx="30" cy="26" r="5"/><path d="M24 44h12M26 50h8M30 6v5M12 26h5M43 26h5"/></svg>
  </div></div>
  <div class="disc-icon" style="left:539px"><div>
    <svg width="60" height="60" viewBox="0 0 60 60" fill="none" stroke="#fff" stroke-width="2.5"><rect x="8" y="10" width="44" height="30"/><path d="M16 34V26M23 34V20M30 34V24"/><circle cx="40" cy="26" r="6"/><path d="M44 30l6 6M30 40v10M22 52l8-6 8 6"/></svg>
  </div></div>
  <div class="disc-icon" style="left:872px"><div>
    <svg width="60" height="60" viewBox="0 0 60 60" fill="none" stroke="#fff" stroke-width="2.5"><rect x="12" y="6" width="36" height="20"/><path d="M18 14h16M18 20h10"/><circle cx="14" cy="38" r="4"/><circle cx="26" cy="38" r="4"/><circle cx="38" cy="38" r="4"/><circle cx="50" cy="38" r="4"/><path d="M9 52v-6h10v6M21 52v-6h10v6M33 52v-6h10v6M45 52v-6h10v6"/></svg>
  </div></div>

  <div class="disc-go" style="left:245px"><svg width="14" height="14" viewBox="0 0 16 16"><circle cx="8" cy="8" r="8" fill="#fff"/><path d="M6.5 4.5 10 8l-3.5 3.5" stroke="#0a63b8" stroke-width="2" fill="none"/></svg></div>
  <div class="disc-go" style="left:579px"><svg width="14" height="14" viewBox="0 0 16 16"><circle cx="8" cy="8" r="8" fill="#fff"/><path d="M6.5 4.5 10 8l-3.5 3.5" stroke="#0a63b8" stroke-width="2" fill="none"/></svg></div>
  <div class="disc-go" style="left:912px"><svg width="14" height="14" viewBox="0 0 16 16"><circle cx="8" cy="8" r="8" fill="#fff"/><path d="M6.5 4.5 10 8l-3.5 3.5" stroke="#0a63b8" stroke-width="2" fill="none"/></svg></div>
</section>

<section class="plan">
  <h2 class="heading section-title">The K7 Plan Elements</h2>
  <div class="pill" style="left:130px;top:148px">
    <div class="pill-photo" role="img" aria-label="Team discussing a market analysis" style="background:linear-gradient(135deg,#7a8a9a,#c7a27a)"></div>
    <h4>Market Analysis</h4>
    <p>Displays research and plan to reach the target demographic as well as the size, direction, and competitors in the overall industry.</p>
  </div>
  <div class="pill" style="left:620px;top:148px">
    <div class="pill-photo" role="img" aria-label="Hands reviewing charts on a laptop" style="background:linear-gradient(135deg,#3d4a5a,#a8b0b8)"></div>
    <h4>Operations/Strategy</h4>
    <p>Explains how the company will function given the sales and marketing strategy, and the plan of operations from acquisition of suppliers to delivery, including</p>
  </div>
  <div class="pill" style="left:130px;top:320px">
    <div class="pill-photo" role="img" aria-label="Executive reviewing financial statements" style="background:linear-gradient(135deg,#8fa3b6,#e0e4e8)"></div>
    <h4>Financials</h4>
    <p>Details estimates of all the important, financial documents, including balance sheet, cash flow, statement, capital, expenditure, budget, and income.</p>
  </div>
  <div class="pill" style="left:620px;top:320px">
    <div class="pill-photo" role="img" aria-label="Management team meeting around a presentation" style="background:linear-gradient(135deg,#c4d0da,#8aa07a)"></div>
    <h4 style="top:36px">Organization &amp; Management Team</h4>
    <p style="top:62px">Shows the company structure as well as identifying divisions and key management personnel.</p>
  </div>
  <a class="btn btn-white view-more">View &nbsp;More
    <svg viewBox="0 0 16 16"><circle cx="8" cy="8" r="8" fill="#0a63b8"/><path d="M6.5 4.5 10 8l-3.5 3.5" stroke="#fff" stroke-width="2" fill="none"/></svg>
  </a>
</section>

<footer class="site-footer">
  <div class="footer-brand"><span class="brand-dot" style="background:#3d8be0"></span>The K7 Momentum<br>Collective</div>
  <div class="socials"><span></span><span></span><span></span><span></span></div>

  <div class="f-col" style="left:422px">
    <h5>Quick Links</h5>
    <ul><li>Home</li><li>About Us</li><li>Services</li><li>Team</li><li>Contact Us</li></ul>
  </div>
  <div class="f-col" style="left:630px">
    <h5>Other links</h5>
    <ul><li>FAQ</li><li>Support</li><li>Terms &amp; Condition</li><li>Contact Us</li><li>Privacy Policy</li></ul>
  </div>
  <div class="f-col" style="left:848px;width:270px">
    <h5>Contact Us</h5>
    <div class="contact-item">
      <svg viewBox="0 0 16 16"><path d="M3 1h3l1.5 4-2 1.2a9 9 0 0 0 4.3 4.3L11 8.5l4 1.5v3a2 2 0 0 1-2 2A13 13 0 0 1 1 3a2 2 0 0 1 2-2z" fill="#3d8be0"/></svg>
      <b>Phone</b><span>+1 555 014 2290</span>
    </div>
    <div class="contact-item">
      <svg viewBox="0 0 16 16"><rect x="1" y="3" width="14" height="10" rx="1" fill="#3d8be0"/><path d="M1.5 4 8 9l6.5-5" stroke="#2c2c2c" stroke-width="1.3" fill="none"/></svg>
      <b>Email</b><span>info@k7momentumcollective.com</span>
    </div>
    <div class="contact-item">
      <svg viewBox="0 0 16 16"><path d="M8 1a5 5 0 0 1 5 5c0 4-5 9-5 9S3 10 3 6a5 5 0 0 1 5-5z" fill="#3d8be0"/><circle cx="8" cy="6" r="2" fill="#2c2c2c"/></svg>
      <b>Location</b><span>59 Lorem ipsum dolor sit ameted consectetur elit, sed do</span>
    </div>
  </div>

  <div class="f-rule"></div>
  <div class="to-top"><svg width="16" height="16" viewBox="0 0 16 16"><path d="M3 10.5 8 5.5l5 5" stroke="#fff" stroke-width="2" fill="none"/></svg></div>
  <p class="copyright">2023 Copyright - The K7 Momentum Collective &nbsp;| All Rights Reserved</p>
</footer>

</body>
</html>
```